Modern Business Card

Modern professional business card with more than just logo and demographic info. Something memorable.

We are a trendy/modern chiropractic group with an emphasis on neurology, hence the minimalist-type brain logo. We want to convey that modern and technical aspect with professionalism and the elite nature of our practice environment.

```html
<!DOCTYPE html>
<html lang="en">
<head>
<meta charset="utf-8">
<title>Kestrel Chiropractic – Business Card</title>
<link href="https://fonts.googleapis.com/css2?family=Lora:wght@400;700&family=Montserrat:wght@400&display=swap" rel="stylesheet">
<style>
  :root {
    --brand-blue: #4680c2;
    --ink: #2b2b2b;
    --ink-soft: #4a4a4a;
    --band-grey: #3d3d3f;
    --paper: #ffffff;
    --backdrop: #5a5a5c;
  }
  * { margin: 0; padding: 0; box-sizing: border-box; }
  html, body { width: 1200px; height: 901px; overflow: hidden; }
  body { background: var(--backdrop); position: relative; font-family: "Montserrat", sans-serif; }

  .card {
    position: absolute; left: 280px; width: 640px; height: 366px;
    overflow: hidden; box-shadow: 0 8px 22px rgba(0,0,0,.35);
  }
  .card--front { top: 64px; background: var(--brand-blue); }
  .card--back { top: 472px; background: var(--paper); }

  .wordmark { position: absolute; display: flex; align-items: center; gap: 14px; }
  .wordmark__mark { width: 34px; height: 34px; }
  .wordmark__text {
    font-family: "Lora", serif; font-weight: 400; line-height: .95;
    letter-spacing: 2px; text-transform: uppercase;
  }
  .wordmark__line1 { display: block; font-size: 46px; }
  .wordmark__line2 { display: block; font-size: 25px; letter-spacing: 2.6px; }

  .card--front .wordmark { left: 50%; top: 50%; transform: translate(-50%, -50%); }
  .card--front .wordmark__mark { background: var(--paper); }
  .card--front .wordmark__text { color: var(--paper); }

  .card--back .wordmark { left: 50%; top: 74px; transform: translateX(-50%); }
  .card--back .wordmark__mark { background: var(--brand-blue); }
  .card--back .wordmark__text { color: var(--ink); }

  .holder {
    position: absolute; right: 336px; top: 208px; text-align: right;
  }
  .holder__name {
    font-family: "Lora", serif; font-weight: 700; font-size: 22px;
    color: var(--brand-blue); letter-spacing: .5px; text-transform: uppercase;
  }
  .holder__role, .holder__address { font-size: 12.5px; color: var(--ink-soft); line-height: 1.45; }
  .holder__role { margin-bottom: 2px; }

  .divider {
    position: absolute; left: 324px; top: 206px; width: 1.5px; height: 86px;
    background: var(--brand-blue);
  }

  .contacts { position: absolute; left: 342px; top: 208px; list-style: none; }
  .contacts li {
    display: flex; align-items: center; gap: 8px;
    font-size: 12.5px; color: var(--ink-soft); line-height: 20.5px;
  }
  .contacts svg { width: 11px; height: 11px; fill: var(--brand-blue); flex: none; }

  .edge-band { position: absolute; left: 0; bottom: 0; width: 640px; height: 26px; }
</style>
</head>
<body>

  <section class="card card--front" aria-label="Card front">
    <div class="wordmark">
      <span class="wordmark__mark"></span>
      <span class="wordmark__text">
        <span class="wordmark__line1">Kestrel</span>
        <span class="wordmark__line2">Chiropractic</span>
      </span>
    </div>
  </section>

  <section class="card card--back" aria-label="Card back">
    <div class="wordmark">
      <span class="wordmark__mark"></span>
      <span class="wordmark__text">
        <span class="wordmark__line1">Kestrel</span>
        <span class="wordmark__line2">Chiropractic</span>
      </span>
    </div>

    <div class="holder">
      <p class="holder__name">Thomas Avery</p>
      <p class="holder__role">Senior Partner</p>
      <p class="holder__address">12 Harrow Lane Northvale<br>Lakeside, 4310</p>
    </div>

    <span class="divider"></span>

    <ul class="contacts">
      <li>
        <svg viewBox="0 0 24 24" aria-hidden="true"><path d="M6.6 10.8a15 15 0 0 0 6.6 6.6l2.2-2.2c.3-.3.7-.4 1-.2 1.1.4 2.3.6 3.6.6.6 0 1 .4 1 1V20c0 .6-.4 1-1 1A17 17 0 0 1 3 4c0-.6.4-1 1-1h3.5c.6 0 1 .4 1 1 0 1.3.2 2.5.6 3.6.1.3 0 .7-.2 1z"/></svg>
        +120 5550 1187
      </li>
      <li>
        <svg viewBox="0 0 24 24" aria-hidden="true"><path d="M7 1h10a2 2 0 0 1 2 2v18a2 2 0 0 1-2 2H7a2 2 0 0 1-2-2V3a2 2 0 0 1 2-2zm0 3v14h10V4zm5 15.5a1 1 0 1 0 0 2 1 1 0 0 0 0-2z"/></svg>
        +965 5550 2294
      </li>
      <li>
        <svg viewBox="0 0 24 24" aria-hidden="true"><path d="M2 5h20v14H2zm2 2v.4l8 5.2 8-5.2V7zm0 2.8V17h16V9.8l-8 5.2z"/></svg>
        info@kestrelchiropractic.com
      </li>
      <li>
        <svg viewBox="0 0 24 24" aria-hidden="true"><path d="M12 2a10 10 0 1 0 0 20 10 10 0 0 0 0-20zm6.9 6h-2.9a15 15 0 0 0-1.4-3.6A8 8 0 0 1 18.9 8zM12 4c.8 1.2 1.5 2.5 1.9 4h-3.8c.4-1.5 1.1-2.8 1.9-4zM4.3 14a8 8 0 0 1 0-4h3.4a16 16 0 0 0 0 4zm.8 2h2.9c.3 1.3.8 2.5 1.4 3.6A8 8 0 0 1 5.1 16zM8 8H5.1a8 8 0 0 1 4.3-3.6C8.8 5.5 8.4 6.7 8 8zm4 12c-.8-1.2-1.5-2.5-1.9-4h3.8c-.4 1.5-1.1 2.8-1.9 4zm2.3-6H9.7a14 14 0 0 1 0-4h4.6a14 14 0 0 1 0 4zm.3 5.6c.6-1.1 1.1-2.3 1.4-3.6h2.9a8 8 0 0 1-4.3 3.6zm1.7-5.6a16 16 0 0 0 0-4h3.4a8 8 0 0 1 0 4z"/></svg>
        www.kestrelchiropractic.com
      </li>
    </ul>

    <svg class="edge-band" viewBox="0 0 640 26" aria-hidden="true">
      <rect x="0" y="18" width="386" height="8" fill="var(--brand-blue)"/>
      <polygon points="386,18 394,18 386,26" fill="var(--brand-blue)"/>
      <polygon points="392,26 402,4 640,4 640,26" fill="var(--band-grey)"/>
    </svg>
  </section>

</body>
</html>
```